Local massage therapist needs some new marketing material

Hi there! I am a massage therapist here in Denver, CO in Alder Bend(shopping and art district) of the city. My business is called Lumo Bodywork of Denver. My practice has an eastern influence and I do reflexology, thai massage and use Chinese herbs, etc. I know all my clients and pay close attention to details. I am also very respectful of tradition and it shows in how I work. I tend to like modern, clean, fun, Asian designs. I am wanting a new business card and brochure. I have a logo and branding for my business that I want used in the design. Currently, the sign for my building is purple and I think my logo was designed to be purple. I will attach pictures of it and can send whatever files are necessary so it can be integrated into the brochure, etc. I like the purple but open to using other colors as well. Thanks!
My website is lumobodyworkofdenver.example where info can be gathered about me and services/fees for brochure.
Updates

Just increased budget. Please see new feedback in discussion thread.

Thanks!

                                       HEY ALL,

Just wanted to let you know that I made a change to my website. It is on the Prices Page. I no longer have the frequent  flyer prices but I added discounts. Let me know if you have any questions. Thanks so much!

Target Market(s)

healthy, urban, educated, upper middle class, yogis

Industry/Entity Type

Marketing

Requirements
Must have
• logo stays purple
Should not have
• not too busy

```html
<!DOCTYPE html>
<html lang="en">
<head>
<meta charset="utf-8">
<title>Lumo Bodywork of Denver – Business Card</title>
<link href="https://fonts.googleapis.com/css2?family=Open+Sans:ital,wght@0,400;0,600;0,700;1,400&display=swap" rel="stylesheet">
<style>
  :root {
    --purple: #5e2d91;
    --ink: #444448;
    --swoosh-dark: #2b2b2e;
    --swoosh-grey: #9a9aa0;
    --paper: #ffffff;
    --backdrop: #e8e8ee;
    --rule: #9c9ca4;
  }
  * { margin: 0; padding: 0; box-sizing: border-box; }
  html, body { width: 1200px; height: 987px; overflow: hidden; }
  body {
    background: var(--backdrop);
    font-family: "Open Sans", Arial, sans-serif;
    color: var(--ink);
    position: relative;
  }
  .card {
    position: absolute;
    left: 250px;
    width: 700px;
    height: 400px;
    background: var(--paper);
    border-radius: 40px;
    overflow: hidden;
    box-shadow: 0 4px 14px rgba(0,0,0,0.12);
  }
  .card-front { top: 50px; }
  .card-back { top: 530px; }

  .brand {
    position: absolute;
    display: flex;
    align-items: center;
    gap: 16px;
    color: var(--purple);
    font-weight: 400;
    letter-spacing: 10px;
  }
  .brand-dot {
    width: 22px; height: 22px;
    border-radius: 50%;
    background: var(--purple);
  }
  .card-front .brand { left: 70px; top: 55px; font-size: 72px; }
  .card-back .brand { right: 50px; top: 250px; font-size: 58px; }

  .wave { position: absolute; inset: 0; }

  .holder { position: absolute; left: 40px; top: 300px; color: var(--paper); }
  .holder-name { font-size: 24px; font-weight: 700; line-height: 1.2; }
  .holder-title { font-size: 15px; }

  .address {
    position: absolute; right: 50px; top: 180px;
    text-align: right; font-size: 20px; line-height: 1.35;
  }
  .contacts {
    position: absolute; right: 45px; top: 300px;
    color: var(--paper); font-size: 19px; line-height: 1.45;
    text-align: right;
  }
  .contact-line { display: flex; justify-content: flex-end; align-items: center; gap: 8px; }
  .contact-line svg { width: 16px; height: 16px; }

  .appointment { position: absolute; left: 50px; top: 40px; right: 50px; font-size: 18px; }
  .appointment-heading {
    color: var(--purple); font-weight: 700; font-size: 17px;
    letter-spacing: 0.5px; margin-bottom: 16px;
  }
  .field-row { display: flex; align-items: flex-end; gap: 8px; margin-bottom: 14px; }
  .field-line { flex: 1; border-bottom: 1px dotted var(--rule); height: 20px; }
  .field-line.short { flex: 0 0 200px; }
  .hours { margin-top: 10px; line-height: 1.45; width: 420px; }
  .note { font-style: italic; font-size: 16px; margin-top: 8px; color: #6a6a70; }
</style>
</head>
<body>

<section class="card card-front" aria-label="Business card front">
  <svg class="wave" viewBox="0 0 700 400" aria-hidden="true">
    <path d="M0,108 C30,228 130,262 310,250 C490,238 620,250 700,296" fill="none" stroke="var(--swoosh-grey)" stroke-width="3"/>
    <path d="M0,116 C32,238 132,270 310,262 C490,252 620,262 700,306" fill="none" stroke="var(--swoosh-dark)" stroke-width="6"/>
    <path d="M0,128 C36,252 136,284 310,276 C490,268 620,276 700,318 L700,400 L0,400 Z" fill="var(--purple)"/>
  </svg>

  <div class="brand"><span class="brand-name">LUMO</span><span class="brand-dot"></span></div>

  <div class="address">1457 E Larkin Ave, Denver<br>CO 80299</div>

  <div class="holder">
    <div class="holder-name">Your Name</div>
    <div class="holder-title">Title</div>
  </div>

  <div class="contacts">
    <div class="contact-line">
      <svg viewBox="0 0 16 16" aria-hidden="true"><path d="M4 1.5l2.2 3-1.3 1.6c.9 1.9 2.4 3.4 4.3 4.3l1.6-1.3 3 2.2-1.2 2.8C7.6 14 2 8.4 1.2 2.7z" fill="currentColor"/></svg>
      <span>303.555.0147</span>
    </div>
    <div class="contact-line">
      <svg viewBox="0 0 16 16" aria-hidden="true"><rect x="1.5" y="3.5" width="13" height="9" rx="1" fill="none" stroke="currentColor" stroke-width="1.5"/><path d="M2 4l6 5 6-5" fill="none" stroke="currentColor" stroke-width="1.5"/></svg>
      <span>info@lumobodyworkofdenver.example</span>
    </div>
    <div class="contact-line">
      <svg viewBox="0 0 16 16" aria-hidden="true"><circle cx="8" cy="8" r="6.5" fill="none" stroke="currentColor" stroke-width="1.4"/><ellipse cx="8" cy="8" rx="3" ry="6.5" fill="none" stroke="currentColor" stroke-width="1.2"/><path d="M1.5 8h13" stroke="currentColor" stroke-width="1.2"/></svg>
      <span>www.lumobodyworkofdenver.example</span>
    </div>
  </div>
</section>

<section class="card card-back" aria-label="Business card back">
  <div class="appointment">
    <div class="appointment-heading">YOUR APPOINTMENT</div>
    <div class="field-row"><span>Name :</span><span class="field-line"></span></div>
    <div class="field-row"><span>Date :</span><span class="field-line short"></span><span>Time :</span><span class="field-line"></span><span>am / pm</span></div>
    <p class="hours">Tues - Fri 10am - 8pm Sat 10am-5pm<br>(Appointments required) No walk-ins please.</p>
    <p class="note">We appreciate a 24 hr. notice for cancellations</p>
  </div>
  <div class="brand"><span class="brand-name">LUMO</span><span class="brand-dot"></span></div>
</section>

</body>
</html>
```